Letterhead Design Project

I need letterhead designed for my law firm. It would also be used for web based stuff as well.

Industry/Entity Type

Law Firm

```html
<!DOCTYPE html>
<html lang="en">
<head>
<meta charset="UTF-8">
<title>Hargrove &amp; Lenz Letterhead</title>
<link rel="stylesheet" href="https://fonts.googleapis.com/css2?family=Didact+Gothic&display=swap">
<style>
  :root {
    --band-dark: #1b2528;
    --band-mid: #2c3a3e;
    --paper: #ffffff;
    --texture-light: #fbfbfb;
    --texture-tone: #f2f3f3;
    --name-ink: #f4f6f7;
    --footer-ink: #5a5f63;
    --divider: #8a8f93;
  }
  html, body {
    margin: 0;
    padding: 0;
    overflow: hidden;
    background: var(--paper);
  }
  .letterhead {
    position: relative;
    width: 906px;
    height: 1200px;
    overflow: hidden;
    background: var(--paper);
    font-family: "Didact Gothic", "Century Gothic", sans-serif;
  }
  .header-band {
    position: absolute;
    top: 0;
    left: 0;
    width: 906px;
    height: 48px;
    background: linear-gradient(90deg, var(--band-mid) 0%, var(--band-dark) 55%, var(--band-dark) 100%);
  }
  .firm-name {
    position: absolute;
    right: 14px;
    top: 9px;
    margin: 0;
    font-size: 27px;
    font-weight: 400;
    font-variant: small-caps;
    letter-spacing: 1px;
    line-height: 30px;
    color: var(--name-ink);
  }
  .page-texture {
    position: absolute;
    top: 48px;
    left: 0;
    width: 906px;
    height: 1110px;
    background: linear-gradient(180deg, var(--texture-tone) 0%, var(--texture-light) 60%, var(--paper) 100%);
  }
  .footer-contact {
    position: absolute;
    left: 0;
    right: 0;
    bottom: 14px;
    text-align: center;
    font-size: 15.5px;
    color: var(--footer-ink);
    white-space: nowrap;
  }
  .footer-contact .divider {
    display: inline-block;
    margin: 0 18px;
    color: var(--divider);
  }
  .footer-contact .gap {
    display: inline-block;
    width: 10px;
  }
</style>
</head>
<body>
  <div class="letterhead">
    <header class="header-band">
      <h1 class="firm-name">Hargrove &amp; Lenz</h1>
    </header>
    <div class="page-texture" role="img" aria-label="Faint light grey lattice texture across the page"></div>
    <footer class="footer-contact">
      <span class="address">238 Linden Avenue NW&nbsp; Washington, DC 20011</span>
      <span class="divider">|</span>
      <span class="phone">Phone (202) 555-0148</span><span class="gap"></span><span class="toll-free">Toll Free: 855-555-0172</span>
    </footer>
  </div>
</body>
</html>
```